BorrowNest Website design, we are a home loan / lending company

We are a finance broking company that can do mortgages / home loans, Car Loans, Commercial Loans, SMSF Loans, Business Loans, Personal Loans
We are looking for a simple website, not too busy, easy to navigate, something that prompts customers to action or call us.
I like the simplicity of the following websites:
https://www.velkarafinance.com.au/ - I like this website front page. I was thinking I have my logo, the one with the black background appear , then the toolbar at the top perhaps?
https://trevix.com.au/business-loans# - on this page there are images under finance that works for you that I like that concept.
https://dunmerel.com.au/contact/ - I like the Make an Appointment page
https://trevix.com.au/about-us - Simple but effective page design

Target Market(s)

Home Loan Customer

Industry/Entity Type

Finance / Home Loans

Coding

Coded - Design and coding required

Number of Pages Required

5+ page

Font styles to use
Serif

Colors
0094D4
00A9DD
6FCCEA
C7EBF8
E9F6FB

Requirements
Must have
• The following Heading s - Contact Us, About Us, Our People, Make an Appointment, Loan Options, Calculators, Reviews. I want to use the Logo colours I have in the zip files I uploaded.
Nice to have
• Simple clean design

```html
<!DOCTYPE html>
<html lang="en">
<head>
<meta charset="utf-8">
<title>BorrowNest — Home Loans &amp; Lending</title>
<link href="https://fonts.googleapis.com/css2?family=Outfit:wght@400;500;600;700&display=swap" rel="stylesheet">
<style>
:root{
  --navy:#0b1426;
  --ink:#1f2733;
  --text:#555b63;
  --blue:#0094d4;
  --blue-2:#00a9dd;
  --blue-3:#6fccea;
  --blue-pale:#c7ebf8;
  --blue-mist:#e9f6fb;
  --card-blue:#1a9be0;
  --dark-btn:#2a323d;
  --line:#dcdfe3;
  --grey-bg:#f3f4f6;
  --star:#1e8a3a;
}
*{box-sizing:border-box;margin:0;padding:0}
html,body{width:1200px;height:4335px;overflow:hidden}
body{font-family:"Outfit",sans-serif;color:var(--ink);background:#fff;position:relative}
.abs{position:absolute}
p,.body-text{font-family:Arial,Helvetica,sans-serif}

/* header */
.topbar{left:0;top:0;width:1200px;height:106px;background:var(--navy)}
.brand{font-family:"Outfit",sans-serif;font-weight:600;color:#fff;letter-spacing:-.5px}
.topbar .brand{left:111px;top:28px;font-size:40px;line-height:50px}
.social{display:flex;gap:10px}
.social span{width:32px;height:32px;border:1.5px solid #fff;border-radius:50%;display:block}
.topbar .social{left:666px;top:36px}
.appt-btn{left:847px;top:27px;width:240px;height:48px;border:2px solid var(--blue-2);border-radius:24px;color:#fff;font-size:15px;font-weight:500;display:flex;align-items:center;justify-content:center;letter-spacing:.3px}

.mainnav{left:0;top:106px;width:1200px;height:54px;background:linear-gradient(180deg,#29b9f0,#1aa4e6)}
.navlinks{display:flex;justify-content:space-between;align-items:center;list-style:none}
.mainnav .navlinks{position:absolute;left:152px;width:896px;top:0;height:54px}
.navlinks li{font-size:14px;font-weight:500;color:#fff;letter-spacing:.2px;position:relative;height:100%;display:flex;align-items:center}
.mainnav li.active::after{content:"";position:absolute;left:-6px;right:-6px;bottom:0;height:4px;background:var(--navy)}

/* hero */
.hero{left:0;top:160px;width:1200px;height:676px;overflow:hidden}
.hero-photo{position:absolute;inset:0;background:linear-gradient(90deg,#3b3f44 0%,#5a5e63 30%,#9aa3ab 52%,#dfe4e8 66%,#f5f7f8 78%,#fafbfc 100%)}
.hero h1{left:745px;top:250px;font-size:66px;font-weight:600;color:var(--ink);line-height:80px;letter-spacing:-.5px}
.hero .lead{left:747px;top:340px;width:440px;font-family:"Outfit",sans-serif;font-size:22px;line-height:34px;color:#444}
.pill-btn{border-radius:30px;display:flex;align-items:center;justify-content:center}
.hero .pill-btn{left:747px;top:432px;width:170px;height:54px;background:linear-gradient(90deg,var(--blue),var(--blue-2));color:#fff;font-size:18px;font-weight:500}

/* section titles */
.sec-title{width:1200px;left:0;text-align:center;font-size:40px;font-weight:500;color:var(--ink)}
.sec-title em{font-style:normal;color:var(--blue)}
.sec-title.light{color:#fff}
.title-rule{width:52px;height:3px;background:var(--blue);left:574px}
.title-rule.white{background:#fff}

/* services */
.services-intro{left:300px;width:600px;top:936px;text-align:center;font-size:15px;line-height:28px;color:var(--text)}
.service-card{width:306px;height:362px;background:#fff;border:1px solid var(--line);text-align:center}
.service-card::before{content:"";position:absolute;left:-1px;top:-1px;width:64px;height:20px;border-top:2px solid var(--blue);border-left:2px solid var(--blue)}
.service-card::after{content:"";position:absolute;right:-1px;bottom:-1px;width:64px;height:62px;border-bottom:2px solid var(--blue);border-right:2px solid var(--blue)}
.service-card .icon{position:absolute;left:113px;top:36px;width:80px;height:80px}
.service-card h3{position:absolute;top:136px;width:100%;font-size:21px;font-weight:500;color:var(--ink)}
.service-card p{position:absolute;top:178px;left:20px;right:20px;font-size:13.5px;line-height:28px;color:var(--text)}
.service-card .card-btn{position:absolute;left:86px;top:280px;width:134px;height:46px;border:1px solid var(--blue);border-radius:23px;font-size:16px;font-weight:500;display:flex;align-items:center;justify-content:center;color:var(--ink)}
.service-card.featured{background:var(--card-blue);border-color:var(--card-blue)}
.service-card.featured::before{border-color:var(--navy)}
.service-card.featured::after{border-color:var(--navy)}
.service-card.featured h3,.service-card.featured p{color:#fff}
.service-card.featured .card-btn{background:var(--dark-btn);border-color:var(--dark-btn);color:#fff}
.icon svg{width:80px;height:80px;fill:none;stroke:var(--ink);stroke-width:2.2;stroke-linecap:round;stroke-linejoin:round}
.icon svg .acc{stroke:var(--blue)}
.featured .icon svg,.featured .icon svg .acc{stroke:#fff}

/* loan options */
.loan-options{left:0;top:1885px;width:1200px;height:505px;background:linear-gradient(90deg,#eef1f4 0%,#e7ebef 45%,#dfe5ea 100%)}
.loan-photo{position:absolute;left:505px;top:0;width:695px;height:505px;background:linear-gradient(90deg,rgba(223,229,234,0) 0%,#c9d0d8 35%,#6d7683 62%,#9aa3ad 80%,#d9dee3 100%)}
.loan-options h2{left:111px;top:78px;font-size:38px;font-weight:500}
.loan-options h2 em{font-style:normal;color:var(--blue)}
.loan-options .rule{left:111px;top:133px;width:98px;height:3px;background:var(--ink)}
.checklist{left:111px;top:170px;list-style:none}
.checklist li{display:flex;align-items:center;height:44.6px;font-size:17px;color:var(--ink)}
.checklist svg{width:17px;height:17px;margin-right:22px;margin-left:0}

/* calculator */
.calculator{left:0;top:2390px;width:1200px;height:485px;background:linear-gradient(135deg,#1c9ee3 0%,#1592dc 55%,#1a9be0 100%)}
.calc-label{font-size:15px;color:#fff}
.calc-input{background:#fff;border-radius:26px;height:51px;display:flex;align-items:center;padding-left:26px;font-size:16px;color:var(--ink)}
.calc-help{font-size:13px;color:var(--blue-pale)}
.rate-badge{border:1px solid #fff;border-radius:17px;color:#fff;font-size:14px;display:flex;align-items:center;justify-content:center}
.slider-track{height:10px;border-radius:5px;background:var(--dark-btn)}
.slider-fill{height:10px;border-radius:5px;background:#fff}
.slider-knob{width:30px;height:30px;border-radius:50%;background:#fff;border:4px solid var(--dark-btn)}
.calc-btn{background:var(--dark-btn);color:#fff;border-radius:25px;font-size:16px;font-weight:500;display:flex;align-items:center;justify-content:center}

/* reviews */
.review{width:296px}
.review .meta{display:flex;justify-content:space-between;align-items:center;height:18px}
.stars{display:flex;gap:2px}
.stars svg{width:14px;height:14px;fill:var(--star)}
.review .when{font-family:Arial,sans-serif;font-size:13px;color:var(--text)}
.review h4{margin-top:14px;font-family:Arial,sans-serif;font-size:15px;font-weight:700;color:var(--ink)}
.review p{margin-top:14px;font-size:13px;line-height:25px;color:var(--text);text-align:justify}
.review .author{display:block;margin-top:20px;font-family:Arial,sans-serif;font-size:14px;font-weight:700;color:var(--blue);text-decoration:underline}

/* people */
.people{left:0;top:3329px;width:1200px;height:528px;background:var(--grey-bg)}
.person{width:303px;height:343px;background:#fff;border:1px solid var(--line);text-align:center}
.person .photo{height:257px;background:linear-gradient(160deg,#b8c0c8,#7f8994 55%,#c9ced4)}
.person h5{margin-top:16px;font-size:21px;font-weight:500;color:var(--ink)}
.person .role{margin-top:6px;font-size:14px;color:var(--text)}
.person.featured{background:var(--card-blue);border-color:var(--card-blue)}
.person.featured h5,.person.featured .role{color:#fff}

/* footer */
.footer{left:0;top:3857px;width:1200px;height:478px;background:var(--navy);color:#fff}
.footer .brand{width:1200px;text-align:center;top:44px;left:0;font-size:46px}
.footer .navlinks{position:absolute;left:152px;width:896px;top:160px;height:34px}
.footer .divider{left:111px;top:208px;width:978px;height:1px;background:#24304a}
.footer h6{font-size:19px;font-weight:600;letter-spacing:.3px;text-transform:uppercase}
.contact-line{display:flex;align-items:center;gap:8px;font-size:17px}
.contact-line svg{width:15px;height:15px;fill:var(--blue-2)}
.news-input{background:#fff;color:var(--text);font-size:15px;display:flex;align-items:center;padding-left:26px}
.news-btn{background:var(--blue-2);color:#fff;font-size:15px;font-weight:600;display:flex;align-items:center;justify-content:center}
.footer .social span{border-color:var(--blue-2)}
.copyright{font-size:15px}
</style>
</head>
<body>

<header class="abs topbar">
  <div class="abs brand">BorrowNest</div>
  <div class="abs social" aria-label="Social links"><span></span><span></span><span></span><span></span></div>
  <div class="abs appt-btn">MAKE AN APPOINTMENT</div>
</header>

<nav class="abs mainnav">
  <ul class="navlinks">
    <li class="active">HOME</li><li>ABOUT US</li><li>OUR PEOPLE</li><li>LOAN OPTIONS</li><li>CALCULATORS</li><li>REVIEWS</li><li>CONTACT US</li>
  </ul>
</nav>

<section class="abs hero">
  <div class="hero-photo" role="img" aria-label="Businessman in a suit working at a laptop in an office"></div>
  <h1 class="abs">BorrowNest</h1>
  <p class="abs lead">Sed ut perspiciatis unde omnis iste nat us error sit voluptatem accusa..</p>
  <div class="abs pill-btn">Read More</div>
</section>

<h2 class="abs sec-title" style="top:878px">Our <em>Services</em></h2>
<p class="abs services-intro">Sed ut perspiciatis unde omnis iste natus error sit voluptatem accusantium doloremque laudantium, totam rem aperiam, eaque ipsa</p>

<article class="abs service-card" style="left:111px;top:1035px">
  <div class="icon"><svg viewBox="0 0 80 80"><path d="M6 40 30 18l24 22"/><path d="M12 35v30h36V35"/><path d="M24 65V50h12v15"/><path d="M40 24v-8h6v13"/><circle class="acc" cx="58" cy="44" r="14"/><path class="acc" d="M52 51l12-14"/><circle class="acc" cx="53" cy="39" r="2"/><circle class="acc" cx="63" cy="49" r="2"/></svg></div>
  <h3>Home Loans</h3>
  <p>Sed ut perspiciatis unde omnis iste natus error sit voluptatem accusantium doloremque laudantium, totam</p>
  <div class="card-btn">Read More</div>
</article>
<article class="abs service-card featured" style="left:446px;top:1035px">
  <div class="icon"><svg viewBox="0 0 80 80"><path d="M8 46l6-14c1-3 4-5 7-5h20c3 0 6 2 7 5l4 10"/><path d="M6 48h44v12H6z"/><circle cx="15" cy="54" r="2"/><path d="M12 60v6h8v-6M38 60v6h8v-6"/><path d="M2 36h10M0 42h8"/><path class="acc" d="M72 32c-2-3-6-4-9-3-4 1-4 6 0 7l6 2c5 2 4 8-1 9-3 1-7 0-9-3M65 24v5M65 47v5"/></svg></div>
  <h3>Car Loans</h3>
  <p>Sed ut perspiciatis unde omnis iste natus error sit voluptatem accusantium doloremque laudantium, totam</p>
  <div class="card-btn">Read More</div>
</article>
<article class="abs service-card" style="left:781px;top:1035px">
  <div class="icon"><svg viewBox="0 0 80 80"><path d="M30 72V8h30v64"/><path d="M10 72V36h20"/><path d="M4 72h72"/><path class="acc" d="M38 18h14M38 26h14M38 34h14M38 42h14M38 50h14M38 58h14"/><path d="M16 44h8M16 52h8M16 60h8"/></svg></div>
  <h3>Commercial Loans</h3>
  <p>Sed ut perspiciatis unde omnis iste natus error sit voluptatem accusantium doloremque laudantium, totam</p>
  <div class="card-btn">Read More</div>
</article>

<article class="abs service-card" style="left:111px;top:1439px">
  <div class="icon"><svg viewBox="0 0 80 80"><circle class="acc" cx="42" cy="22" r="16"/><circle class="acc" cx="42" cy="22" r="11"/><path class="acc" d="M46 17c-1-2-6-3-7 0s6 3 6 6-5 3-7 1M42 13v2M42 29v2"/><path d="M6 56l10-8c4-3 8-3 12-1l8 4h10c3 0 3 5 0 5H34"/><path d="M44 58l20-10c4-2 7 3 3 6L46 68H24l-8 6"/></svg></div>
  <h3>SMSF Loans</h3>
  <p>Sed ut perspiciatis unde omnis iste natus error sit voluptatem accusantium doloremque laudantium, totam</p>
  <div class="card-btn">Read More</div>
</article>
<article class="abs service-card" style="left:446px;top:1439px">
  <div class="icon"><svg viewBox="0 0 80 80"><path d="M8 70h50"/><path d="M12 70V38h10v32M26 70V16h10v54M40 70V28h10v18"/><circle class="acc" cx="58" cy="54" r="14"/><path class="acc" d="M52 61l12-14"/><circle class="acc" cx="53" cy="49" r="2"/><circle class="acc" cx="63" cy="59" r="2"/></svg></div>
  <h3>Business Loans</h3>
  <p>Sed ut perspiciatis unde omnis iste natus error sit voluptatem accusantium doloremque laudantium, totam</p>
  <div class="card-btn">Read More</div>
</article>
<article class="abs service-card" style="left:781px;top:1439px">
  <div class="icon"><svg viewBox="0 0 80 80"><circle cx="18" cy="12" r="6"/><path d="M8 44V26c0-4 4-6 10-6s10 2 10 6v18h-5v28h-10V44z"/><path d="M18 52v20"/><path class="acc" d="M38 14l4 4 7-7M38 36l4 4 7-7M38 58l4 4 7-7"/><path class="acc" d="M54 16h18M54 24h12M54 38h18M54 46h12M54 60h18M54 68h12"/></svg></div>
  <h3>Personal Loans</h3>
  <p>Sed ut perspiciatis unde omnis iste natus error sit voluptatem accusantium doloremque laudantium, totam</p>
  <div class="card-btn">Read More</div>
</article>

<section class="abs loan-options">
  <div class="loan-photo" role="img" aria-label="Smiling businessman with clasped hands sitting at a laptop"></div>
  <h2 class="abs">Loan <em>Options</em></h2>
  <div class="abs rule"></div>
  <ul class="abs checklist">
    <li><svg viewBox="0 0 20 20"><circle cx="10" cy="10" r="8.5" fill="none" stroke="#0094d4" stroke-width="2"/><path d="M6 10.5l2.7 2.7L14 8" fill="none" stroke="#0094d4" stroke-width="2.2"/></svg>Borrow $5,000 – $250,000</li>
    <li><svg viewBox="0 0 20 20"><circle cx="10" cy="10" r="8.5" fill="none" stroke="#0094d4" stroke-width="2"/><path d="M6 10.5l2.7 2.7L14 8" fill="none" stroke="#0094d4" stroke-width="2.2"/></svg>12 – 24 month loan terms</li>
    <li><svg viewBox="0 0 20 20"><circle cx="10" cy="10" r="8.5" fill="none" stroke="#0094d4" stroke-width="2"/><path d="M6 10.5l2.7 2.7L14 8" fill="none" stroke="#0094d4" stroke-width="2.2"/></svg>No asset security required</li>
    <li><svg viewBox="0 0 20 20"><circle cx="10" cy="10" r="8.5" fill="none" stroke="#0094d4" stroke-width="2"/><path d="M6 10.5l2.7 2.7L14 8" fill="none" stroke="#0094d4" stroke-width="2.2"/></svg>Apply online in 7 minutes</li>
    <li><svg viewBox="0 0 20 20"><circle cx="10" cy="10" r="8.5" fill="none" stroke="#0094d4" stroke-width="2"/><path d="M6 10.5l2.7 2.7L14 8" fill="none" stroke="#0094d4" stroke-width="2.2"/></svg>Credit decisions within 24 hours</li>
    <li><svg viewBox="0 0 20 20"><circle cx="10" cy="10" r="8.5" fill="none" stroke="#0094d4" stroke-width="2"/><path d="M6 10.5l2.7 2.7L14 8" fill="none" stroke="#0094d4" stroke-width="2.2"/></svg>No penalty for early repayment</li>
  </ul>
</section>

<section class="abs calculator">
  <h2 class="abs sec-title light" style="top:44px;font-size:38px">Loan Calculater</h2>
  <div class="abs title-rule white" style="top:101px"></div>
  <div class="abs calc-label" style="left:364px;top:133px">Loan amount</div>
  <div class="abs calc-input" style="left:352px;top:161px;width:247px">$50000</div>
  <div class="abs calc-help" style="left:364px;top:221px">Min $5,000 - Max $250,000</div>
  <div class="abs calc-label" style="left:638px;top:133px">Loan term</div>
  <div class="abs calc-input" style="left:626px;top:161px;width:222px">12 month</div>
  <div class="abs calc-help" style="left:638px;top:221px">Min 12 months - Max 24 months</div>
  <div class="abs calc-label" style="left:364px;top:271px">Interest rate <svg width="13" height="13" viewBox="0 0 14 14" style="vertical-align:-1px"><circle cx="7" cy="7" r="7" fill="#fff"/><path d="M7 6v4.5M7 3.5v1" stroke="#1592dc" stroke-width="1.8"/></svg></div>
  <div class="abs rate-badge" style="left:747px;top:267px;width:101px;height:34px">24.95%</div>
  <div class="abs slider-track" style="left:364px;top:311px;width:488px"></div>
  <div class="abs slider-fill" style="left:364px;top:311px;width:220px"></div>
  <div class="abs slider-knob" style="left:566px;top:301px"></div>
  <div class="abs calc-btn" style="left:500px;top:375px;width:200px;height:50px">Calculate Now</div>
</section>

<h2 class="abs sec-title" style="top:2908px">Our <em>Reviews</em></h2>
<div class="abs title-rule" style="top:2966px"></div>

<article class="abs review" style="left:111px;top:3041px">
  <div class="meta"><div class="stars"><svg viewBox="0 0 20 20"><path d="M10 1l2.6 6 6.4.6-4.9 4.3 1.5 6.3L10 15l-5.6 3.2 1.5-6.3L1 7.6 7.4 7z"/></svg><svg viewBox="0 0 20 20"><path d="M10 1l2.6 6 6.4.6-4.9 4.3 1.5 6.3L10 15l-5.6 3.2 1.5-6.3L1 7.6 7.4 7z"/></svg><svg viewBox="0 0 20 20"><path d="M10 1l2.6 6 6.4.6-4.9 4.3 1.5 6.3L10 15l-5.6 3.2 1.5-6.3L1 7.6 7.4 7z"/></svg><svg viewBox="0 0 20 20"><path d="M10 1l2.6 6 6.4.6-4.9 4.3 1.5 6.3L10 15l-5.6 3.2 1.5-6.3L1 7.6 7.4 7z"/></svg><svg viewBox="0 0 20 20"><path d="M10 1l2.6 6 6.4.6-4.9 4.3 1.5 6.3L10 15l-5.6 3.2 1.5-6.3L1 7.6 7.4 7z"/></svg></div><span class="when">5 days ago</span></div>
  <h4>Sed ut perspiciatis unde</h4>
  <p>Sed ut perspiciatis unde omnis iste natus error sit voluptatem accusantium doloremque laudanti um, totam rem aperiam, eaque ipsa quae ab illo invent ore veritatis et quasi architecto beatae vitae dicta unde omnis sunt explicabo.</p>
  <span class="author">Rowan Tillby</span>
</article>
<article class="abs review" style="left:451px;top:3041px">
  <div class="meta"><div class="stars"><svg viewBox="0 0 20 20"><path d="M10 1l2.6 6 6.4.6-4.9 4.3 1.5 6.3L10 15l-5.6 3.2 1.5-6.3L1 7.6 7.4 7z"/></svg><svg viewBox="0 0 20 20"><path d="M10 1l2.6 6 6.4.6-4.9 4.3 1.5 6.3L10 15l-5.6 3.2 1.5-6.3L1 7.6 7.4 7z"/></svg><svg viewBox="0 0 20 20"><path d="M10 1l2.6 6 6.4.6-4.9 4.3 1.5 6.3L10 15l-5.6 3.2 1.5-6.3L1 7.6 7.4 7z"/></svg><svg viewBox="0 0 20 20"><path d="M10 1l2.6 6 6.4.6-4.9 4.3 1.5 6.3L10 15l-5.6 3.2 1.5-6.3L1 7.6 7.4 7z"/></svg><svg viewBox="0 0 20 20"><path d="M10 1l2.6 6 6.4.6-4.9 4.3 1.5 6.3L10 15l-5.6 3.2 1.5-6.3L1 7.6 7.4 7z"/></svg></div><span class="when">5 days ago</span></div>
  <h4>Sed ut perspiciatis unde</h4>
  <p>Sed ut perspiciatis unde omnis iste natus error sit voluptatem accusantium doloremque laudanti um, totam rem aperiam, eaque ipsa quae ab illo invent ore veritatis et quasi architecto beatae vitae dicta unde omnis sunt explicabo.</p>
  <span class="author">Rowan Tillby</span>
</article>
<article class="abs review" style="left:791px;top:3041px">
  <div class="meta"><div class="stars"><svg viewBox="0 0 20 20"><path d="M10 1l2.6 6 6.4.6-4.9 4.3 1.5 6.3L10 15l-5.6 3.2 1.5-6.3L1 7.6 7.4 7z"/></svg><svg viewBox="0 0 20 20"><path d="M10 1l2.6 6 6.4.6-4.9 4.3 1.5 6.3L10 15l-5.6 3.2 1.5-6.3L1 7.6 7.4 7z"/></svg><svg viewBox="0 0 20 20"><path d="M10 1l2.6 6 6.4.6-4.9 4.3 1.5 6.3L10 15l-5.6 3.2 1.5-6.3L1 7.6 7.4 7z"/></svg><svg viewBox="0 0 20 20"><path d="M10 1l2.6 6 6.4.6-4.9 4.3 1.5 6.3L10 15l-5.6 3.2 1.5-6.3L1 7.6 7.4 7z"/></svg><svg viewBox="0 0 20 20"><path d="M10 1l2.6 6 6.4.6-4.9 4.3 1.5 6.3L10 15l-5.6 3.2 1.5-6.3L1 7.6 7.4 7z"/></svg></div><span class="when">5 days ago</span></div>
  <h4>Sed ut perspiciatis unde</h4>
  <p>Sed ut perspiciatis unde omnis iste natus error sit voluptatem accusantium doloremque laudanti um, totam rem aperiam, eaque ipsa quae ab illo invent ore veritatis et quasi architecto beatae vitae dicta unde omnis sunt explicabo.</p>
  <span class="author">Rowan Tillby</span>
</article>

<section class="abs people">
  <h2 class="abs sec-title" style="top:30px">Our <em>People</em></h2>
  <div class="abs title-rule" style="top:86px"></div>
  <article class="abs person" style="left:111px;top:118px">
    <div class="photo" role="img" aria-label="Portrait of a smiling team member with glasses in a library office"></div>
    <h5>Rowan Tillby</h5><div class="role body-text">Sed ut perspiciatis unde</div>
  </article>
  <article class="abs person featured" style="left:449px;top:118px">
    <div class="photo" role="img" aria-label="Portrait of a smiling team member holding a tablet in an office"></div>
    <h5>Rowan Tillby</h5><div class="role body-text">Sed ut perspiciatis unde</div>
  </article>
  <article class="abs person" style="left:786px;top:118px">
    <div class="photo" role="img" aria-label="Portrait of a team member with crossed arms in a bright office"></div>
    <h5>Rowan Tillby</h5><div class="role body-text">Sed ut perspiciatis unde</div>
  </article>
</section>

<footer class="abs footer">
  <div class="abs brand">BorrowNest</div>
  <ul class="navlinks">
    <li>HOME</li><li>ABOUT US</li><li>OUR PEOPLE</li><li>LOAN OPTIONS</li><li>CALCULATORS</li><li>REVIEWS</li><li>CONTACT US</li>
  </ul>
  <div class="abs divider"></div>
  <h6 class="abs" style="left:111px;top:254px">Contact us for your free estimate</h6>
  <div class="abs contact-line" style="left:111px;top:292px">
    <svg viewBox="0 0 16 16"><path d="M3.6 1l2.6 3.2-1.5 1.9c.9 2 2.5 3.6 4.5 4.5l1.9-1.5L14.3 11.7 12.8 14.5C6.6 14.2 1.8 9.4 1.5 3.2z"/></svg>+1 555 010 2040
    <svg viewBox="0 0 16 16" style="margin-left:14px"><path d="M1 3h14v10H1z"/><path d="M1 3l7 6 7-6" fill="none" stroke="#0b1426" stroke-width="1.4"/></svg>info@borrownest.com
  </div>
  <div class="abs contact-line" style="left:111px;top:328px">
    <svg viewBox="0 0 16 16"><path d="M8 0a5.5 5.5 0 0 0-5.5 5.5C2.5 9.6 8 16 8 16s5.5-6.4 5.5-10.5A5.5 5.5 0 0 0 8 0zm0 7.7a2.2 2.2 0 1 1 0-4.4 2.2 2.2 0 0 1 0 4.4z"/></svg>Lorem Ipsum Dummy Lorem Ipsum
  </div>
  <h6 class="abs" style="left:705px;top:248px">Sign up newsletter</h6>
  <div class="abs news-input" style="left:705px;top:310px;width:254px;height:46px">Enter Email</div>
  <div class="abs news-btn" style="left:959px;top:310px;width:128px;height:46px">SUBSCRIBE</div>
  <div class="abs copyright" style="left:111px;top:426px">© 2022 BorrowNest.All Rights Reserved.</div>
  <div class="abs social" style="left:888px;top:420px;gap:9px" aria-label="Social links"><span></span><span></span><span></span><span></span><span></span></div>
</footer>

</body>
</html>
```